Event flyer for Sunday night Youth Group

Need a 4 x 6 or 5 x 7 flyer for a new youth group starting on April 14. The youth group is for students in middle school and high school so it needs to look fun and cool, but not childish. I prefer it not to include pictures of people unless it's so obscure you can't really see their faces. I've uploaded some pictures of flyers I like. I've also attached a couple versions of our logo to use on the flyer.
Information the flyer needs to include:
Youth Group
Sundays, 6-8pm (beginning April 14)
Location: Marlowe's - 4219 Quarry Fern Ave N, Keizer, 97318
There will be dinner, games, friends, and a message.
Target Market(s)
Youth ages 13-18
Industry/Entity Type
Church
Font styles to use
Colors
Designer to choose colors to be used in the design.
Look and feel

```html
<!DOCTYPE html>
<html lang="en">
<head>
<meta charset="utf-8">
<title>Youth Group – Wayside Fellowship</title>
<link href="https://fonts.googleapis.com/css2?family=Anton&family=Poppins:wght@500;600&display=swap" rel="stylesheet">
<style>
  :root {
    --ink: #17202a;
    --red: #e3102a;
    --red-deep: #8e1324;
    --sage: #8a9a86;
    --white: #ffffff;
    --grey: #a7a9ac;
    --gold: #ffcc00;
  }
  html, body { margin: 0; padding: 0; overflow: hidden; background: var(--ink); }
  .flyer {
    position: relative;
    width: 857px;
    height: 1200px;
    overflow: hidden;
    background: var(--ink);
    font-family: "Poppins", sans-serif;
    color: var(--white);
  }
  .backdrop { position: absolute; inset: 0; }
  .church-name {
    position: absolute;
    left: 0; right: 0; top: 360px;
    text-align: center;
    font-weight: 500;
    font-size: 22px;
    letter-spacing: 4px;
    line-height: 1.35;
    text-transform: uppercase;
  }
  .church-mark {
    position: absolute;
    left: 413px; top: 312px;
    width: 32px; height: 32px;
    background: var(--white);
  }
  .title-main, .title-sub {
    position: absolute;
    left: 0; right: 0;
    text-align: center;
    font-family: "Anton", sans-serif;
    text-transform: uppercase;
    line-height: 1;
  }
  .title-main { top: 462px; font-size: 124px; letter-spacing: 1px; color: var(--white); }
  .title-sub { top: 577px; font-size: 66px; color: var(--grey); }
  .schedule {
    position: absolute;
    left: 181px; top: 655px;
    width: 491px; height: 88px;
    border: 2px solid var(--white);
    border-radius: 30px;
  }
  .schedule-time {
    position: absolute;
    left: 0; right: 0; top: 10px;
    text-align: center;
    font-weight: 600;
    font-size: 39px;
    color: var(--gold);
    line-height: 1.2;
  }
  .schedule-start {
    position: absolute;
    left: 50%; bottom: -17px;
    transform: translateX(-50%);
    padding: 0 12px;
    background: var(--ink);
    font-weight: 500;
    font-size: 24px;
    white-space: nowrap;
    line-height: 1.3;
  }
  .venue {
    position: absolute;
    left: 0; right: 0; top: 786px;
    text-align: center;
    font-weight: 600;
    font-size: 29px;
    line-height: 40px;
    color: var(--red);
  }
  .details {
    position: absolute;
    left: 0; right: 0; top: 888px;
    text-align: center;
    font-weight: 500;
    font-size: 18.5px;
  }
</style>
</head>
<body>
<div class="flyer">
  <svg class="backdrop" viewBox="0 0 857 1200" width="857" height="1200" aria-hidden="true">
    <defs>
      <linearGradient id="fadeTop" x1="0" y1="0" x2="0" y2="1">
        <stop offset="0" stop-color="#e3102a" stop-opacity="0.55"/>
        <stop offset="1" stop-color="#e3102a" stop-opacity="0"/>
      </linearGradient>
      <linearGradient id="fadeBottom" x1="0" y1="1" x2="0" y2="0">
        <stop offset="0" stop-color="#e3102a" stop-opacity="0.55"/>
        <stop offset="1" stop-color="#e3102a" stop-opacity="0"/>
      </linearGradient>
    </defs>
    <!-- top chevrons -->
    <polygon points="0,120 439,559 857,141 857,101 439,519 0,80" fill="url(#fadeTop)"/>
    <polygon points="0,60 439,499 857,81 857,35 439,453 0,14" fill="url(#fadeTop)"/>
    <polygon points="0,0 60,0 439,379 796,0 857,0 857,0 439,418 0,0" fill="url(#fadeTop)"/>
    <polygon points="161,0 439,278 717,0 576,0 439,137 302,0" fill="#d90f28"/>
    <polygon points="415,0 439,24 463,0" fill="#d90f28"/>
    <!-- bottom chevrons -->
    <polygon points="0,1040 439,601 857,1019 857,1059 439,641 0,1080" fill="url(#fadeBottom)"/>
    <polygon points="0,1110 439,671 857,1089 857,1135 439,717 0,1156" fill="url(#fadeBottom)"/>
    <polygon points="0,1200 60,1200 439,821 796,1200 857,1200 439,782 0,1200" fill="url(#fadeBottom)"/>
    <polygon points="230,1200 439,991 648,1200 550,1200 439,1089 328,1200" fill="#d90f28"/>
    <polygon points="373,1200 439,1134 505,1200" fill="#d90f28"/>
    <!-- outline shapes -->
    <g fill="none" stroke="#8a9a86" stroke-width="3">
      <rect x="116" y="99" width="42" height="42"/>
      <rect x="608" y="1036" width="41" height="41"/>
      <circle cx="267" cy="154" r="12"/>
      <circle cx="770" cy="130" r="12"/>
      <circle cx="734" cy="343" r="22"/>
      <circle cx="119" cy="415" r="12"/>
      <circle cx="746" cy="587" r="12"/>
      <circle cx="63" cy="945" r="12"/>
      <circle cx="534" cy="1045" r="12"/>
    </g>
  </svg>

  <div class="church-mark"></div>
  <div class="church-name">Wayside<br>Fellowship</div>

  <div class="title-main">Youth</div>
  <div class="title-sub">Group</div>

  <div class="schedule">
    <div class="schedule-time">Sundays, 6-8pm</div>
    <div class="schedule-start">beginning April 14</div>
  </div>

  <div class="venue">Marlowe's - 4219 Quarry Fern Ave N,<br>Keizer, 97318</div>

  <div class="details">There will be dinner, games, friends, and a message.</div>
</div>
</body>
</html>
```